Business Cards for new orthopaedic surgery practice

My husband and I are starting our own orthopaedic surgery practice. We are looking for a business card that is uniform, but one will have my name/title and the other will have his. You can just create one design with my name on it for now. But when I choose your design as the winning design I will ask that you add another copy with his name/title.

We are looking for classy, simple, elite all in one. We like dark blues/a little gold/yellow. Something that goes with our logo. We want our logo incorporated. Here is all the info you need:
Business name: RV Bone & Vitality Center
Location: 38517 North Willowmere Ave
Palm Hollow, FL 33482
Phone: 954-218-4063
Fax: 954-582-7341
Email: info@myrvbonecare.example

Names: Lydia Vance, M.D.
Board Certified Hand and Upper Extremity Surgeon

Ebo Dansu, M.D.
Board Certified Hip & Knee Replacement/General Orthopaedic Surgeon

Can decide what you want to put on the back. Maybe a slogan:
Rooted in Care. Focused on You

I am just going to upload our logo. The only thing is if we select you as the winning design, the location, and phone numbers may change. We will need your help to update that once fully solidified.

Industry/Entity Type

Medical

Contact Information for Business Card

Colors
0054AA
0677BA
7BADD7
CADEEF
E8F1F8
0094D4
00A9DD
6FCCEA
C7EBF8
E9F6FB

Requirements
Must have
• class, appeal,
Should not have
• We want to air on the side of masculine if we are looking at masculine vs. feminine feel. But we still want it classy, sophisticated, and something we will love

```html
<!DOCTYPE html>
<html lang="en">
<head>
<meta charset="utf-8">
<title>RV Bone &amp; Vitality Center – Business Card</title>
<link href="https://fonts.googleapis.com/css2?family=Poppins:wght@400;500;600&family=Roboto:wght@500&display=swap" rel="stylesheet">
<style>
  :root {
    --navy: #1c2a50;
    --gold: #c8a462;
    --white: #ffffff;
    --backdrop: #e2e8ea;
  }
  * { margin: 0; padding: 0; box-sizing: border-box; }
  html, body { width: 1200px; height: 960px; overflow: hidden; }
  body {
    background: var(--backdrop);
    font-family: "Poppins", sans-serif;
    position: relative;
  }
  .card {
    position: absolute;
    left: 248px;
    width: 704px;
    height: 402px;
    border-radius: 34px;
    overflow: hidden;
    box-shadow: 0 10px 22px rgba(0,0,0,0.25);
  }
  /* Front */
  .card-front { top: 58px; background: var(--navy); color: var(--white); }
  .front-brand {
    position: absolute;
    left: 0; right: 0; top: 118px;
    display: flex; flex-direction: column; align-items: center; gap: 14px;
  }
  .brand-dot {
    width: 20px; height: 20px; border-radius: 50%;
    background: var(--white);
  }
  .front-brand .brand-name {
    font-weight: 500;
    font-size: 26px;
    letter-spacing: 0.06em;
    text-transform: uppercase;
    text-align: center;
    line-height: 1.3;
  }
  .tagline {
    position: absolute;
    left: 0; right: 0; top: 356px;
    text-align: center;
    font-size: 15.5px;
    letter-spacing: 0.03em;
  }
  .tagline .bullet {
    display: inline-block; width: 7px; height: 7px; border-radius: 50%;
    background: var(--white); margin: 0 6px 2px 0; vertical-align: middle;
  }
  .tagline .bullet + span { margin-right: 8px; }

  /* Back */
  .card-back { top: 500px; background: var(--white); color: var(--navy); }
  .gold-band {
    position: absolute; top: 0; right: 0; bottom: 0; width: 232px;
    background: var(--gold);
  }
  .back-brand {
    position: absolute; left: 22px; top: 52px; width: 190px;
    display: flex; flex-direction: column; align-items: center; gap: 8px;
  }
  .back-brand .brand-dot { background: var(--navy); width: 14px; height: 14px; }
  .back-brand .brand-name {
    font-weight: 500; font-size: 15px; letter-spacing: 0.05em;
    text-transform: uppercase; text-align: center; line-height: 1.35;
    color: var(--navy);
  }
  .feature-name {
    position: absolute; left: 300px; top: 120px; width: 380px;
    font-weight: 600; font-size: 46px; line-height: 1.1;
    color: var(--navy); text-transform: uppercase; letter-spacing: 0.02em;
  }
  .id-bar {
    position: absolute; left: 0; top: 171px; width: 14px; height: 56px;
    background: var(--gold);
  }
  .person { position: absolute; left: 20px; top: 170px; }
  .person-name {
    font-family: "Roboto", sans-serif; font-weight: 500;
    font-size: 20.5px; color: var(--gold); line-height: 1.2;
  }
  .person-title { font-size: 13.4px; line-height: 1.3; color: var(--navy); }
  .address {
    position: absolute; left: 20px; top: 238px;
    font-size: 16px; line-height: 1.38; color: var(--gold); letter-spacing: 0.02em;
  }
  .contacts {
    position: absolute; left: 20px; top: 302px; list-style: none;
    font-size: 16px; line-height: 21.7px; color: var(--navy); letter-spacing: 0.02em;
  }
  .contacts li { display: flex; align-items: center; gap: 10px; }
  .contacts svg { width: 16px; height: 16px; flex: none; }
</style>
</head>
<body>

<section class="card card-front" aria-label="Card front">
  <div class="front-brand">
    <span class="brand-dot"></span>
    <p class="brand-name">RV Bone &amp;<br>Vitality Center</p>
  </div>
  <p class="tagline"><span class="bullet"></span><span>Grounded in Trust</span><span class="bullet"></span><span>Centered on You</span></p>
</section>

<section class="card card-back" aria-label="Card back">
  <div class="gold-band"></div>
  <div class="back-brand">
    <span class="brand-dot"></span>
    <p class="brand-name">RV Bone &amp;<br>Vitality Center</p>
  </div>
  <p class="feature-name">RV Bone &amp; Vitality Center</p>

  <div class="id-bar"></div>
  <div class="person">
    <p class="person-name">Ebo Dansu, M.D.</p>
    <p class="person-title">Hip &amp; Knee Replacement<br>/General Orthopaedic Surgery</p>
  </div>

  <p class="address">38517 North Willowmere Ave<br>Palm Hollow, FL 33482</p>

  <ul class="contacts">
    <li>
      <svg viewBox="0 0 16 16" fill="none" stroke="#c8a462" stroke-width="1.5"><path d="M3 2l3 .5 1 3-1.5 1.2a8 8 0 0 0 3.8 3.8L10.5 9l3 1 .5 3-2 1.5C6.5 14 2 9.5 1.5 4z"/></svg>
      <span>954-218-4063</span>
    </li>
    <li>
      <svg viewBox="0 0 16 16" fill="none" stroke="#c8a462" stroke-width="1.5"><rect x="1.5" y="6" width="13" height="8" rx="1"/><rect x="4.5" y="2" width="7" height="4"/><path d="M4 9h2M8 9h2M4 11.5h2M8 11.5h2"/></svg>
      <span>954-582-7341</span>
    </li>
    <li>
      <svg viewBox="0 0 16 16" fill="none" stroke="#c8a462" stroke-width="1.4"><circle cx="8" cy="8" r="6.5"/><ellipse cx="8" cy="8" rx="3" ry="6.5"/><path d="M1.5 8h13M2.5 5h11M2.5 11h11"/></svg>
      <span>www.myrvbonecare.example</span>
    </li>
    <li>
      <svg viewBox="0 0 16 16" fill="none" stroke="#c8a462" stroke-width="1.5"><rect x="1.5" y="4" width="13" height="10" rx="1"/><path d="M1.5 4.5L8 9.5l6.5-5"/></svg>
      <span>info@myrvbonecare.example</span>
    </li>
  </ul>
</section>

</body>
</html>
```